Business Card for Multi-Brand Sportswear Company

We are looking for a business card which represents our company and the multiple brands within it.

The company: Fen Athletics (LTD)
The brands: Fen, TavaPuni, ElmStretch, Grit and Rain

Employees using these cards would be representing Fen Athletics, rather than any of the individual brands. You will see a current design within the uploaded files, to give some inspiration. The actual text of the brands is not necessary, but the logos should be on there is some format.

Our creative minds on this are stretched, so we are looking for someone to make this their own, and show us what a good business card should look like.

We may like to get these printed with spot gloss, so keep that in mind with your designs.

www.fenathletics.co.uk

Industry/Entity Type

Business

Contact Information for Business Card

Leo Pemberton-Hale
Operations Manager
(+44) 1632 960 418
Leo@fenathletics.co.uk
www.fenathletics.co.uk

Font styles to use
Sans Serif
Other font styles liked:
• Eurostile

Colors
ffffff

Requirements
Nice to have
• Dark (black) background

```html
<!DOCTYPE html>
<html lang="en">
<head>
<meta charset="utf-8">
<title>Fen Athletics Business Card</title>
<link rel="stylesheet" href="https://fonts.googleapis.com/css2?family=Michroma&family=Exo+2:wght@400;500;600&display=swap">
<style>
  :root {
    --backdrop: #3a332f;
    --card: #1c1d20;
    --card-edge: #121214;
    --white: #ffffff;
    --silver: #c9c9cb;
    --grey: #a9a9ad;
    --muted: #6f7076;
    --red: #e3212d;
    --purple: #6a5a86;
  }
  * { box-sizing: border-box; margin: 0; padding: 0; }
  html, body { width: 1200px; height: 769px; overflow: hidden; }
  body {
    background: var(--backdrop);
    font-family: "Exo 2", sans-serif;
    color: var(--white);
    position: relative;
  }
  .card {
    position: absolute;
    top: 225px;
    width: 540px;
    height: 310px;
    background: var(--card);
    border-radius: 4px;
    box-shadow: 0 14px 30px rgba(0,0,0,.45);
    overflow: hidden;
  }
  .card--front { left: 40px; }
  .card--back { left: 620px; }

  .wordmark {
    position: absolute;
    font-family: "Michroma", sans-serif;
    text-transform: uppercase;
    letter-spacing: 1px;
  }
  .card--front .wordmark { left: 150px; top: 62px; font-size: 30px; color: var(--white); }
  .tagline {
    position: absolute;
    font-family: "Exo 2", sans-serif;
    text-transform: uppercase;
    letter-spacing: 3px;
    font-size: 11px;
    color: var(--grey);
  }
  .card--front .tagline { left: 300px; top: 108px; }

  .person { position: absolute; left: 40px; top: 196px; }
  .person__name { font-size: 22px; font-weight: 600; color: var(--red); text-transform: uppercase; letter-spacing: .5px; }
  .person__role { font-size: 15px; color: var(--grey); margin-top: 2px; }

  .contact { position: absolute; left: 300px; top: 150px; list-style: none; font-size: 13px; color: var(--grey); line-height: 1.35; }
  .contact li { display: flex; align-items: flex-start; gap: 10px; margin-bottom: 4px; }
  .contact svg { width: 12px; height: 12px; flex: none; margin-top: 2px; fill: var(--red); }

  .band { position: absolute; left: 0; right: 0; bottom: 0; height: 22px; background: var(--red); }
  .band__slashes { position: absolute; right: 14px; bottom: 22px; width: 46px; height: 14px; }

  .card--back .wordmark { left: 0; right: 0; top: 92px; text-align: center; font-size: 40px; color: var(--silver); }
  .card--back .tagline { left: 0; right: 0; top: 150px; text-align: center; color: var(--muted); }

  .brands { position: absolute; left: 30px; right: 30px; bottom: 40px; display: flex; justify-content: space-between; align-items: center; list-style: none; font-size: 14px; font-weight: 500; }
  .brands li { display: flex; align-items: center; gap: 6px; }
  .brand--fen { color: var(--white); }
  .brand--tava { color: var(--grey); }
  .brand--tava .mark { width: 12px; height: 12px; border: 1.5px solid var(--grey); border-radius: 50%; }
  .brand--elm { color: #b7a9d2; }
  .brand--elm .mark { width: 12px; height: 12px; background: var(--purple); }
  .brand--grit { color: var(--red); }
</style>
</head>
<body>
  <section class="card card--front">
    <div class="wordmark">Fen Athletics</div>
    <div class="tagline">Performance Wear</div>

    <div class="person">
      <div class="person__name">Ross Whitfield</div>
      <div class="person__role">Managing Director</div>
    </div>

    <ul class="contact">
      <li>
        <svg viewBox="0 0 12 12" aria-hidden="true"><path d="M6 0a4 4 0 0 0-4 4c0 3 4 8 4 8s4-5 4-8a4 4 0 0 0-4-4zm0 5.5A1.5 1.5 0 1 1 6 2.5a1.5 1.5 0 0 1 0 3z"/></svg>
        <span>Lark Meadow, Eastby<br>Ashwick, ZZ9 4QT</span>
      </li>
      <li>
        <svg viewBox="0 0 12 12" aria-hidden="true"><path d="M2.5 0 4.5 2.5 3.3 4a7 7 0 0 0 4.7 4.7L9.5 7.5 12 9.5 10.5 12C5 12 0 7 0 1.5z"/></svg>
        <span>+44 (0)1632 960418</span>
      </li>
      <li>
        <svg viewBox="0 0 12 12" aria-hidden="true"><path d="M0 2h12v8H0zM1 3l5 3.5L11 3"/></svg>
        <span>ross@fenathletics.co.uk</span>
      </li>
      <li>
        <svg viewBox="0 0 12 12" aria-hidden="true"><circle cx="6" cy="6" r="6"/></svg>
        <span>www.fenathletics.co.uk</span>
      </li>
    </ul>

    <svg class="band__slashes" viewBox="0 0 46 14" aria-hidden="true">
      <polygon points="6,14 12,0 17,0 11,14" fill="#ffffff"/>
      <polygon points="20,14 26,0 31,0 25,14" fill="#ffffff"/>
      <polygon points="34,14 40,0 46,0 40,14" fill="#e3212d"/>
    </svg>
    <div class="band"></div>
  </section>

  <section class="card card--back">
    <div class="wordmark">Fen Athletics</div>
    <div class="tagline">Performance Wear</div>
    <ul class="brands">
      <li class="brand--fen">Fen</li>
      <li class="brand--tava"><span class="mark"></span>TavaPuni</li>
      <li class="brand--elm"><span class="mark"></span>ElmStretch</li>
      <li class="brand--grit">Grit and Rain</li>
    </ul>
  </section>
</body>
</html>
```